Fairway Circuit web site

Fairway Circuit is a High End golf amateur Tour targeted to wealthy golf passionates.
The concept is to take average golfers and offer them the same playing conditions than the pros (Caddies, branded bags, TV coverage...) and bring them to the most beautiful golf courses around the world.
Keywords: International, Exclusive, Luxury, but not show-off...
The Task is to design the WordPress template and a exemple page.
Please use the provided logo and any stock image you like.
Updates

Hello,

please note that the outcome has to be a fully coded WordPress site.

Please no "Photoshop only" designs...

Thanks

```html
<!DOCTYPE html>
<html lang="en">
<head>
<meta charset="utf-8">
<title>Fairway Circuit</title>
<link href="https://fonts.googleapis.com/css2?family=Open+Sans:wght@400;600;700&family=PT+Sans+Narrow:wght@700&display=swap" rel="stylesheet">
<style>
:root{
  --green:#1d6a48;
  --green-dark:#0f4a31;
  --green-deep:#0c3d28;
  --gold:#c89a4e;
  --gold-light:#dcb473;
  --gold-dark:#a77a34;
  --text:#333;
  --muted:#666;
  --line:#ddd;
}
*{margin:0;padding:0;box-sizing:border-box}
html,body{width:778px;height:1200px;overflow:hidden}
body{position:relative;font-family:'Open Sans',sans-serif;color:var(--text);background:#fff}
.abs{position:absolute}
.header{left:0;top:0;width:778px;height:70px;background:linear-gradient(#1f7350,#155c3e)}
.social{top:13px;right:83px;display:flex;gap:4px}
.social span{width:17px;height:17px;border-radius:50%;background:#fff;display:block}
.search{left:540px;top:40px;width:159px;height:19px;border:1px solid #4b8a6c;background:#16583b;color:#9fc0b0;font-size:7px;font-style:italic;padding:4px 6px}
.search svg{position:absolute;right:5px;top:4px}
.nav{left:0;top:70px;width:778px;height:37px;background:linear-gradient(var(--gold-light),var(--gold-dark))}
.nav a{position:absolute;top:0;height:37px;line-height:37px;color:#fff;font-size:11px;font-weight:600;text-decoration:none;text-transform:uppercase}
.nav .sep{position:absolute;top:0;width:1px;height:37px;background:rgba(255,255,255,.25)}
.logo{left:322px;top:10px;width:124px;height:124px;border-radius:50%;background:var(--green);border:4px solid var(--gold);display:flex;align-items:center;justify-content:center;text-align:center;color:#fff;font-weight:700;font-size:15px;line-height:1.2;text-transform:uppercase;z-index:2}
.hero{left:0;top:107px;width:778px;height:289px;background:linear-gradient(#cfe0ec 0%,#8fc0d8 38%,#3e9aa6 48%,#7fbd3a 60%,#4d9a22 100%)}
.hero h1{position:absolute;top:100px;width:100%;text-align:center;color:#fff;font-weight:600;font-size:27px;letter-spacing:.5px;text-shadow:0 1px 3px rgba(0,0,0,.3)}
.hero h2{position:absolute;top:138px;width:100%;text-align:center;color:#fff;font-weight:400;font-size:20px;text-shadow:0 1px 3px rgba(0,0,0,.3)}
.dots{left:367px;top:274px;display:flex;gap:3px}
.dots span{width:9px;height:9px;border-radius:50%;background:#fff}
.cards-band{left:0;top:396px;width:778px;height:178px;background:linear-gradient(90deg,#eee,#fff 20%,#fff 80%,#eee)}
.cards{left:72px;top:396px;width:634px;height:178px;background:#fff;border:1px solid #e4e4e4;border-top:0}
.card{top:407px;height:145px}
.card .photo{height:91px}
.card .label{height:54px;padding:6px 11px;color:#fff}
.card h3{font-size:12.5px;font-weight:600;text-transform:uppercase}
.card p{font-size:7.3px;line-height:12px}
.g{background:var(--green)}
.o{background:var(--gold)}
.video{left:474px;top:405px;width:222px;height:146px;background:linear-gradient(#4f8a3c,#2f6b2a 60%,#6aa347)}
.section-title{font-family:'PT Sans Narrow',sans-serif;font-weight:700;font-size:17px;color:#333;text-transform:uppercase}
.game .thumb{width:99px;height:59px}
.game h4,.news h4{font-size:10px;font-weight:400;color:#333}
.game p{font-size:7.3px;line-height:13.5px;color:#555;margin-top:2px}
.news p{font-size:7.3px;line-height:13.5px;color:#555;margin-top:2px}
.divider{left:70px;top:773px;width:405px;height:1px;background:var(--line)}
.blog{left:490px;top:594px;width:204px;height:233px;border:1px solid #ddd}
.blog-head{height:32px;background:linear-gradient(var(--green),var(--green-dark));color:#fff;font-weight:700;font-size:13px;padding:7px 15px;text-transform:uppercase;margin:-1px -1px 0}
.post{left:16px;width:180px}
.post .thumb{position:absolute;left:0;top:0;width:49px;height:40px}
.post .txt{position:absolute;left:56px;top:-3px}
.post h5{font-size:8.5px;font-weight:400;color:#333}
.post p{font-size:7.3px;line-height:12.5px;color:#888}
.post b{font-size:7.3px;color:#222;font-weight:700}
.photos{left:490px;top:837px;width:202px;height:79px;background:linear-gradient(var(--gold-light),var(--gold));color:#fff;text-align:center;padding-top:17px}
.photos h3{font-size:15px;font-weight:700;text-transform:uppercase}
.photos p{font-size:7px;line-height:12px;padding:0 12px}
.footer-rule{left:0;top:960px;width:778px;height:6px;background:var(--gold)}
.footer{left:0;top:966px;width:778px;height:192px;background:var(--green)}
.map{left:160px;top:12px;width:420px;height:160px;background:radial-gradient(ellipse at center,rgba(255,255,255,.05),rgba(255,255,255,0) 70%)}
.col{top:47px}
.col h6{font-size:11.5px;font-weight:700;color:#fff;text-transform:uppercase;margin-bottom:4px}
.col li{list-style:none;font-size:7.5px;color:#fff;line-height:15.5px;text-transform:uppercase}
.bottom{left:0;top:1158px;width:778px;height:42px;background:var(--green-deep);color:#c8dcd2;font-size:7.5px;padding:15px 75px}
</style>
</head>
<body>

<div class="abs header"></div>
<div class="abs social"><span></span><span></span><span></span><span></span></div>
<div class="abs search">Type your word
  <svg width="10" height="10" viewBox="0 0 10 10"><circle cx="5.5" cy="4.5" r="3" fill="none" stroke="#9fc0b0" stroke-width="1"/><line x1="3.3" y1="6.7" x2="1" y2="9" stroke="#9fc0b0" stroke-width="1"/></svg>
</div>

<nav class="abs nav">
  <a style="left:90px">Home</a><span class="sep" style="left:131px"></span>
  <a style="left:141px">About us</a><span class="sep" style="left:202px"></span>
  <a style="left:212px">Tournaments</a>
  <a style="left:466px">Recent blog</a><span class="sep" style="left:547px"></span>
  <a style="left:558px">Score</a><span class="sep" style="left:604px"></span>
  <a style="left:615px">Video</a><span class="sep" style="left:657px"></span>
  <a style="left:670px">Photo</a>
</nav>

<div class="abs logo">Fairway<br>Circuit</div>

<section class="abs hero" role="img" aria-label="Woman golfer mid-swing on a seaside course with palm trees">
  <h1>PHASELLUS DOLOR SCELERISQUE TEMPUS</h1>
  <h2>VESTIBULUM LIGULA AUGUE BIBENDUM</h2>
</section>
<div class="abs dots"><span></span><span></span><span></span><span></span></div>

<div class="abs cards-band"></div>
<div class="abs cards"></div>
<div class="abs card" style="left:89px;width:184px">
  <div class="photo" role="img" aria-label="Golfer swinging on a fairway" style="background:linear-gradient(#bcd7ea,#8bb35a 60%,#5f9630)"></div>
  <div class="label g"><h3>Upcoming game</h3><p>Nulla sit amet diam Duis non nunc libero a tempus libero lectus feugiat felis</p></div>
</div>
<div class="abs card" style="left:282px;width:184px">
  <div class="photo" role="img" aria-label="Golf ball on a tee with a club" style="background:linear-gradient(#9fcf6a,#5e9e2e)"></div>
  <div class="label o"><h3>Best scoring</h3><p>Nulla sit amet diam Duis non nunc libero a tempus libero lectus feugiat felis</p></div>
</div>
<div class="abs video" role="img" aria-label="Couple walking the course with golf bags">
  <svg style="position:absolute;left:90px;top:52px" width="42" height="42" viewBox="0 0 42 42"><circle cx="21" cy="21" r="19" fill="rgba(0,0,0,.15)" stroke="#fff" stroke-width="3"/><path d="M16 12 L31 21 L16 30 Z" fill="#fff"/></svg>
</div>

<h2 class="abs section-title" style="left:71px;top:592px">Featured games</h2>
<div class="abs game" style="left:71px;top:621px"><div class="thumb" role="img" aria-label="Golfer at sunset" style="background:linear-gradient(#d8b04a,#4d7a2a)"></div></div>
<div class="abs game" style="left:177px;top:618px"><h4>Nulla sit amet</h4><p>Donec dictum lectus non<br>odio Cras a ante vitaed<br>28 Feb 2014</p></div>
<div class="abs game" style="left:279px;top:620px"><div class="thumb" role="img" aria-label="Golfer swinging under blue sky" style="background:linear-gradient(#a8cde6,#7c9e6a 60%,#5d8a3a)"></div></div>
<div class="abs game" style="left:386px;top:617px"><h4>Nulla sit amet</h4><p>Donec dictum lectus non<br>odio Cras a ante vitaed<br>28 Feb 2014</p></div>
<div class="abs game" style="left:72px;top:693px"><div class="thumb" role="img" aria-label="Golfer silhouette at golden hour" style="background:linear-gradient(#f0b13a,#8a5a1a)"></div></div>
<div class="abs game" style="left:177px;top:693px"><h4>Nulla sit amet</h4><p>Donec dictum lectus non<br>odio Cras a ante vitaed<br>28 Feb 2014</p></div>
<div class="abs game" style="left:279px;top:693px"><div class="thumb" role="img" aria-label="Golfer on a green fairway" style="background:linear-gradient(#d5e2ec,#8bb35a 60%,#5c9030)"></div></div>
<div class="abs game" style="left:386px;top:690px"><h4>Nulla sit amet</h4><p>Donec dictum lectus non<br>odio Cras a ante vitaed<br>28 Feb 2014</p></div>

<div class="abs divider"></div>

<h2 class="abs section-title" style="left:70px;top:788px">News feed</h2>
<div class="abs news" style="left:70px;top:814px"><h4>Aliquam nec erat at purus</h4><p>Pellentesque faucibus Ut accumsan ultricies Maecenas<br>Posted on 28 Feb 2014</p></div>
<div class="abs news" style="left:280px;top:814px"><h4>Aliquam nec erat at purus</h4><p>Pellentesque faucibus Ut accumsan ultricies Maecenas<br>Posted on 28 Feb 2014</p></div>
<div class="abs news" style="left:70px;top:869px"><h4>Aliquam nec erat at purus</h4><p>Pellentesque faucibus Ut accumsan ultricies Maecenas<br>Posted on 28 Feb 2014</p></div>
<div class="abs news" style="left:280px;top:869px"><h4>Aliquam nec erat at purus</h4><p>Pellentesque faucibus Ut accumsan ultricies Maecenas<br>Posted on 28 Feb 2014</p></div>

<aside class="abs blog">
  <div class="blog-head">Recent blog</div>
  <div class="abs post" style="top:42px"><div class="thumb" role="img" aria-label="Gloved hand placing a ball" style="background:linear-gradient(#e8eee8,#6a9a3a)"></div><div class="txt"><h5>Nulla sit amet</h5><p>Maecenas at justo id velit placerat<br>molestie Donec dictum lectus</p><b>11 hours ago</b></div></div>
  <div class="abs post" style="top:105px"><div class="thumb" role="img" aria-label="Golf ball on grass" style="background:linear-gradient(#8cc45a,#4d8a24)"></div><div class="txt"><h5>Nulla sit amet</h5><p>Maecenas at justo id velit placerat<br>molestie Donec dictum lectus</p><b>11 hours ago</b></div></div>
  <div class="abs post" style="top:168px"><div class="thumb" role="img" aria-label="Golfers walking on a course" style="background:linear-gradient(#b9d6ea,#6ea43c)"></div><div class="txt"><h5>Nulla sit amet</h5><p>Maecenas at justo id velit placerat<br>molestie Donec dictum lectus</p><b>11 hours ago</b></div></div>
</aside>

<div class="abs photos"><h3>View our photos</h3><p>Aliquam nec erat at purus cursus interdum Vestibu-lum ligula augue bibendum accumsan</p></div>

<div class="abs footer-rule"></div>
<footer class="abs footer">
  <div class="abs map" role="img" aria-label="Faint world map background"></div>
  <div class="abs col" style="left:82px"><h6>Company</h6><ul><li>Home</li><li>About us</li><li>Upcomin game</li><li>Photos</li><li>Contact us</li></ul></div>
  <div class="abs col" style="left:193px"><h6>Featured game</h6><ul><li>Aliquam nec</li><li>Erat at purus cursus</li><li>Interdum vesti</li><li>Bulum ligula</li><li>Augue bibend</li></ul></div>
  <div class="abs col" style="left:325px"><h6>Support</h6><ul><li>Best players</li><li>Teams</li><li>Awards</li><li>Videos</li><li>Photos</li></ul></div>
  <div class="abs col" style="left:445px"><h6>Sublinks</h6><ul><li>Aliquam</li><li>Purus cursus</li><li>Interdum vesti</li><li>Bulum li</li><li>Augue bibend</li></ul></div>
  <div class="abs col" style="left:578px"><h6>Sublinks</h6><ul><li>Support</li><li>FAQ</li><li>Testimonials</li><li>Recent blog</li><li>Contact</li></ul></div>
</footer>
<div class="abs bottom">© 2014 Company Name.&nbsp; All right reserved.&nbsp; Term of Use</div>

</body>
</html>
```